Fern Gate book design

I would like a new cover design to my book Fern Gate. It is a self help book for teenagers that I give away in public schools while I speak on suicide prevention type topics. I will send you the current cover that has the Fern Gate logo on it. The tag line now says, "raising the value of human life" I want to change that to, "Discovering your Own Worth."

```html
<!DOCTYPE html>
<html lang="en">
<head>
<meta charset="utf-8">
<title>Fern Gate – Book Cover</title>
<link rel="stylesheet" href="https://fonts.googleapis.com/css2?family=Montserrat:wght@500;700&display=swap">
<style>
  :root {
    --stage: #505050;
    --cover-light: #f3f3f3;
    --cover-mid: #dcdcdc;
    --ink: #444444;
    --accent: #8b0000;
    --crowd-red: rgba(165, 75, 75, 0.55);
    --crowd-gray: rgba(120, 115, 115, 0.5);
  }
  * { margin: 0; padding: 0; box-sizing: border-box; }
  html, body {
    width: 1200px;
    height: 800px;
    overflow: hidden;
    background: var(--stage);
  }
  .canvas {
    position: relative;
    width: 1200px;
    height: 800px;
  }
  .book-cover {
    position: absolute;
    left: 344px;
    top: 52px;
    width: 448px;
    height: 671px;
    overflow: hidden;
    border-radius: 3px;
    background:
      radial-gradient(ellipse at 85% 30%, #ffffff 0%, rgba(255,255,255,0) 40%),
      radial-gradient(ellipse at 30% 58%, #fafafa 0%, rgba(255,255,255,0) 45%),
      linear-gradient(170deg, var(--cover-light) 0%, var(--cover-mid) 35%, #ececec 60%, var(--cover-light) 100%);
  }
  .title-block {
    position: absolute;
    left: 76px;
    top: 170px;
    width: 340px;
    height: 140px;
  }
  .title-dot {
    position: absolute;
    left: 0;
    top: 52px;
    width: 24px;
    height: 24px;
    border-radius: 50%;
    background: var(--accent);
  }
  .book-title {
    position: absolute;
    left: 36px;
    top: 0;
    font-family: "Montserrat", sans-serif;
    font-weight: 700;
    font-size: 60px;
    line-height: 58px;
    color: var(--ink);
    text-transform: uppercase;
  }
  .book-title span { display: block; }
  .tagline {
    position: absolute;
    left: 222px;
    top: 64px;
    font-family: "Montserrat", sans-serif;
    font-weight: 500;
    font-size: 15px;
    line-height: 19px;
    color: var(--ink);
    white-space: nowrap;
  }
  .crowd-photo {
    position: absolute;
    left: 0;
    bottom: 0;
    width: 100%;
    height: 270px;
    background:
      radial-gradient(ellipse at 20% 70%, var(--crowd-red) 0%, rgba(165,75,75,0) 55%),
      radial-gradient(ellipse at 45% 85%, rgba(150,60,60,0.5) 0%, rgba(150,60,60,0) 50%),
      radial-gradient(ellipse at 75% 45%, var(--crowd-gray) 0%, rgba(120,115,115,0) 55%),
      radial-gradient(ellipse at 95% 90%, rgba(160,80,80,0.45) 0%, rgba(160,80,80,0) 45%);
    -webkit-mask-image: linear-gradient(to bottom, transparent 0%, #000 35%);
    mask-image: linear-gradient(to bottom, transparent 0%, #000 35%);
  }
</style>
</head>
<body>
  <main class="canvas">
    <section class="book-cover">
      <div class="title-block">
        <span class="title-dot"></span>
        <h1 class="book-title"><span>Fern</span><span>Gate</span></h1>
        <p class="tagline">Discovering<br>your Own Worth</p>
      </div>
      <div class="crowd-photo" role="img" aria-label="Soft-focus photo of a crowd of young people, tinted red and gray"></div>
    </section>
  </main>
</body>
</html>
```